Business Card Design using new attached logo

We are a family run Plumbing and Heating firm looking to improve our company image with an improved business card and new logo.We are looking to keep the company colour (Blue) involved in our design

Reason: New logo added which needs to be incorporated on designs

Industry/Entity Type

Business

Contact Information for Business Card

See attachment of all info required.

Requirements
Must have
• We have just picked a new company logo which is attached.
• Could you please provide your business card designs using this logo.
• We are looking for the logo on the back as well as the front with all the info required

```html
<!DOCTYPE html>
<html lang="en">
<head>
<meta charset="utf-8">
<title>Brookline Services – Business Card</title>
<link rel="stylesheet" href="https://fonts.googleapis.com/css2?family=Open+Sans:wght@400;600;700&display=swap">
<style>
  :root {
    --backdrop: #e8e5e0;
    --brand-blue: #1f4f9c;
    --brand-blue-dark: #143a78;
    --brand-blue-light: #3f86cf;
    --silver: #b9bcc1;
    --silver-light: #e4e6e9;
    --card-white: #fbfbfb;
    --ink: #3c3f44;
    --white: #ffffff;
  }
  * { box-sizing: border-box; margin: 0; padding: 0; }
  html, body { width: 1200px; height: 795px; overflow: hidden; }
  body {
    background: var(--backdrop);
    font-family: "Open Sans", Arial, sans-serif;
    position: relative;
  }
  .card {
    position: absolute;
    top: 247px;
    width: 520px;
    height: 300px;
    border-radius: 18px;
    overflow: hidden;
    box-shadow: 0 6px 18px rgba(0,0,0,0.18);
  }
  .card--front { left: 60px; background: var(--card-white); }
  .card--back {
    left: 620px;
    background: radial-gradient(ellipse at 55% 45%, var(--brand-blue-light) 0%, var(--brand-blue) 45%, var(--brand-blue-dark) 100%);
  }
  .front-art { position: absolute; inset: 0; }

  .holder { position: absolute; left: 26px; top: 206px; color: var(--white); }
  .holder__name { font-weight: 700; font-size: 17px; line-height: 1.2; }
  .holder__role { font-weight: 600; font-size: 12px; margin-left: 22px; margin-top: 2px; }

  .wordmark {
    position: absolute;
    display: flex; align-items: center; gap: 8px;
    font-weight: 700; color: var(--brand-blue);
  }
  .card--front .wordmark { right: 28px; top: 62px; font-size: 24px; }
  .wordmark__dot { width: 14px; height: 14px; border-radius: 50%; background: currentColor; }

  .contact {
    position: absolute; left: 168px; top: 158px;
    font-size: 11px; line-height: 15px; color: var(--ink);
  }
  .contact__address { margin-bottom: 3px; }
  .contact__row { display: flex; align-items: center; gap: 6px; }
  .contact__row svg { width: 10px; height: 10px; fill: var(--brand-blue); flex: none; }

  .card--back .wordmark {
    left: 0; right: 0; top: 128px; justify-content: center;
    font-size: 30px; color: var(--white);
  }
  .card--back .wordmark__dot { width: 16px; height: 16px; }
  .website {
    position: absolute; left: 0; right: 0; bottom: 26px; text-align: center;
    font-size: 12px; letter-spacing: 1px; color: rgba(255,255,255,0.8);
  }
</style>
</head>
<body>
  <section class="card card--front">
    <svg class="front-art" viewBox="0 0 520 300" aria-hidden="true">
      <defs>
        <linearGradient id="band-blue" x1="0" y1="0" x2="1" y2="1">
          <stop offset="0" stop-color="#2a60b0"/>
          <stop offset="1" stop-color="#173f82"/>
        </linearGradient>
        <linearGradient id="band-silver" x1="0" y1="0" x2="1" y2="0">
          <stop offset="0" stop-color="#9ea2a8"/>
          <stop offset="0.5" stop-color="#e4e6e9"/>
          <stop offset="1" stop-color="#b9bcc1"/>
        </linearGradient>
      </defs>
      <path d="M0 0 H165 C118 80 112 200 150 300 H0 Z" fill="url(#band-blue)"/>
      <path d="M165 0 H178 C132 80 126 200 164 300 H150 C112 200 118 80 165 0 Z" fill="url(#band-silver)"/>
    </svg>

    <div class="holder">
      <p class="holder__name">Daniel Hart</p>
      <p class="holder__role">Director</p>
    </div>

    <div class="wordmark"><span class="wordmark__dot"></span>Brookline Services</div>

    <div class="contact">
      <p class="contact__address">Brookline Services Ltd<br>14 Mill Lane, Harbour Road<br>Ashford, AB1 2CD</p>
      <p class="contact__row"><svg viewBox="0 0 10 10"><path d="M2 0.5 L3.6 2.6 L2.8 3.6 C3.4 5 4.8 6.4 6.2 7 L7.2 6.2 L9.4 7.8 L8.2 9.5 C4.6 9.2 0.8 5.4 0.5 1.8 Z"/></svg>020 7946 0312</p>
      <p class="contact__row"><svg viewBox="0 0 10 10"><path d="M1 3 H9 V9 H1 Z M3 0.5 H7 V3 H3 Z"/></svg>020 7946 0415</p>
      <p class="contact__row"><svg viewBox="0 0 10 10"><path d="M3 0.5 H7 A0.8 0.8 0 0 1 7.8 1.3 V8.7 A0.8 0.8 0 0 1 7 9.5 H3 A0.8 0.8 0 0 1 2.2 8.7 V1.3 A0.8 0.8 0 0 1 3 0.5 Z"/></svg>07700 900123</p>
      <p class="contact__row"><svg viewBox="0 0 10 10"><path d="M0.5 2 H9.5 V8 H0.5 Z M0.5 2 L5 5.5 L9.5 2" stroke="#fff" stroke-width="0.8"/></svg>danielhart@brooklineservices.co.uk</p>
    </div>
  </section>

  <section class="card card--back">
    <div class="wordmark"><span class="wordmark__dot"></span>Brookline Services</div>
    <p class="website">www.brooklineservices.co.uk</p>
  </section>
</body>
</html>
```